lum-vex needs updated company presentation for perspective principals

We are looking to update our current company overview presentation that we use for giving new and prospective principals (companies we see for) an overview of our company and our capabilities. We have a PowerPoint presentation but would like to give it a more professional and updated look. There are some modification we'd like to incorporate into the new presentation, but that can be added later.
We will also be looking at using this look to update our website and some additional promotion literature for the near future ( Brochures, Mailers....)
Updates

On the territory overview. I need to increase the state view to include Missouri, Iowa, Kansas, Nebraska, Minnesota and Tennessee. This is the first project we've worked on, so please let me know what additional information is required or makes this process go smoother.

Industry/Entity Type

Chemical Product

Font styles to use
Serif

Colors
ec1f27
000000

Requirements
Must have
• Company History, Territory overview, Industries Served, Principal Represented, Employee overview, Historic Performance

```html
<!DOCTYPE html>
<html lang="en">
<head>
<meta charset="utf-8">
<title>lum-vex, inc. — Company Overview Presentation</title>
<link rel="stylesheet" href="https://fonts.googleapis.com/css2?family=Open+Sans:wght@300;400;700;800&family=Roboto+Condensed:wght@700&display=swap">
<style>
:root{
  --stage:#7a7a7a;
  --stage-dark:#5f5f5f;
  --red:#ec1f27;
  --red-deep:#c0101a;
  --red-dark:#9b141b;
  --black:#231f20;
  --band:#eeeff1;
  --grey:#cbccce;
  --grey-light:#dcdddf;
  --text-muted:#a7a9ac;
  --text-dark:#3a3a3a;
  --amber:#fbb81a;
  --white:#ffffff;
}
*{box-sizing:border-box;margin:0;padding:0}
html,body{width:1200px;height:1200px;overflow:hidden}
body{
  background:linear-gradient(135deg,var(--stage) 0%,var(--stage-dark) 100%);
  font-family:"Open Sans",Arial,sans-serif;
  position:relative;
}
.slide{
  position:absolute;width:515px;height:308px;background:var(--white);overflow:hidden;
}
.slide--cover{left:77px;top:138px}
.slide--history{left:625px;top:138px}
.slide--territory{left:77px;top:478px}
.slide--industries{left:625px;top:478px}
.slide--principals{left:77px;top:818px}
.slide--employees{left:625px;top:818px}

.slide__header{
  position:absolute;left:0;top:0;width:100%;height:48px;
  background:var(--band);border-top:6px solid var(--red-deep);
}
.slide__title{
  position:absolute;left:22px;top:11px;font-size:21px;font-weight:400;color:var(--text-dark);
  letter-spacing:.1px;
}
.slide__badge{
  position:absolute;right:12px;top:9px;width:24px;height:24px;border-radius:50%;
  background:var(--grey-light);border:2px solid var(--grey);
}
.slide__art{position:absolute;left:0;top:0;width:515px;height:308px}

.wordmark{
  position:absolute;font-family:"Open Sans",Arial,sans-serif;font-weight:800;
  color:var(--red);letter-spacing:-.5px;white-space:nowrap;
}
.wordmark--footer{right:14px;bottom:12px;font-size:16px}
.wordmark--cover{left:70px;top:118px;font-size:42px;letter-spacing:-1.5px}
.wordmark--on-red{color:var(--white);right:16px;bottom:12px;font-size:14px}

.tagline{
  position:absolute;left:66px;top:212px;font-family:"Roboto Condensed",Arial,sans-serif;
  font-weight:700;font-size:17px;color:var(--black);
}

.copy{position:absolute;font-size:6.2px;line-height:8.8px;color:var(--text-muted)}
.copy p{margin-bottom:4px}
.copy__kicker{text-transform:uppercase;margin-bottom:5px}
.copy--history{left:36px;top:94px;width:190px}
.copy--territory{left:36px;top:91px;width:188px}
.copy--industries{left:35px;top:78px;width:222px}
.copy--employees{left:35px;top:230px;width:380px}

.map-area{
  position:absolute;left:258px;top:48px;width:257px;height:134px;background:var(--grey);
}
.history-panel{
  position:absolute;left:258px;top:182px;width:257px;height:126px;background:var(--red-deep);
}
.history-panel .copy{left:19px;top:19px;width:222px;color:var(--white);font-size:6.2px}

.bullets{position:absolute;left:122px;top:201px;width:330px;list-style:none}
.bullets li{position:relative;padding-left:13px;font-size:5.8px;line-height:8.6px;color:var(--text-muted);margin-bottom:7px}
.bullets li::before{content:"";position:absolute;left:0;top:2px;width:6px;height:6px;border-radius:50%;background:var(--red-deep)}
.bullets li.is-grey::before{background:var(--grey)}

.chart-label{font-family:"Open Sans",Arial,sans-serif}
</style>
</head>
<body>

<!-- Cover -->
<section class="slide slide--cover">
  <svg class="slide__art" viewBox="0 0 515 308" aria-hidden="true">
    <polygon points="378,0 515,0 515,308 470,308 505,250" fill="var(--black)"/>
    <polygon points="404,0 420,0 500,140 488,150" fill="var(--white)"/>
    <polygon points="420,0 436,0 515,138 515,160" fill="var(--red-deep)"/>
    <polygon points="395,0 404,0 480,132 470,140" fill="var(--red-dark)"/>
    <polygon points="282,308 408,88 430,98 318,308" fill="var(--red-dark)"/>
    <polygon points="318,308 430,98 450,108 352,308" fill="var(--white)"/>
    <polygon points="352,308 450,160 515,160 515,308" fill="var(--grey)"/>
    <polygon points="450,108 515,0 515,60 470,160" fill="var(--red-deep)"/>
  </svg>
  <div class="wordmark wordmark--cover">lum-vex, inc.</div>
  <div class="tagline">Representing the World's Best</div>
</section>

<!-- Company History -->
<section class="slide slide--history">
  <div class="slide__header"><h2 class="slide__title">Company History</h2><span class="slide__badge"></span></div>
  <div class="copy copy--history">
    <p class="copy__kicker">Lorem ipsum dolor</p>
    <p>Morbi fermentum tempor ligula. Phasellus erat est, semper et volutpat a, eleifend id odio. In mollis ultricies massa, a tempus ante luctus sed. Fusce justo leo, convallis et dui sed, mattis venenatis mauris. Phasellus suscipit vel magna sit amet efficitur.</p>
    <p>Donec a ultricies purus. Suspendisse dictum nunc nec magna suscipit bibendum. Maecenas turpis sapien, elementum vitae tellus sit amet, efficitur bibendum tortor. Sed commodo diam ut nisl sodales consectetur. In hac habitasse platea dictumst. Proin ut augue at augue euismod malesuada.</p>
    <p>Donec a metus sed ligula ultrices vulputate. Nullam convallis interdum mi, in ornare ligula vestibulum vel. Donec faucibus, elit eu viverra posuere, libero enim tempus nisi, ac facilisis ligula metus vel ex.</p>
  </div>
  <div class="map-area" role="img" aria-label="World map showing the company's global reach"></div>
  <div class="history-panel">
    <div class="copy">
      <p>Donec a ultricies purus. Suspendisse dictum nunc nec magna suscipit bibendum. Maecenas turpis sapien, elementum vitae tellus sit amet, efficitur bibendum tortor.</p>
      <p>Sed commodo diam ut nisl sodales consectetur. In hac habitasse platea dictumst. Proin ut augue at augue euismod malesuada.</p>
      <p>Donec a metus sed ligula ultrices vulputate. Nullam convallis interdum mi, in ornare ligula vestibulum vel. Donec faucibus, elit eu viverra posuere, libero enim.</p>
    </div>
    <div class="wordmark wordmark--on-red">lum-vex, inc.</div>
  </div>
</section>

<!-- Territory overview -->
<section class="slide slide--territory">
  <div class="slide__header"><h2 class="slide__title">Territory overview</h2><span class="slide__badge"></span></div>
  <div class="copy copy--territory">
    <p class="copy__kicker">Lorem ipsum dolor</p>
    <p>Morbi fermentum tempor ligula. Phasellus erat est, semper et volutpat a, eleifend id odio. In mollis ultricies massa, a tempus ante luctus sed. Fusce justo leo, convallis et dui sed, mattis venenatis mauris. Phasellus suscipit vel magna sit amet efficitur.</p>
    <p>Donec a ultricies purus. Suspendisse dictum nunc nec magna suscipit bibendum. Maecenas turpis sapien, elementum vitae tellus sit amet, efficitur bibendum tortor. Sed commodo diam ut nisl sodales consectetur. In hac habitasse platea dictumst. Proin ut augue at augue euismod malesuada.</p>
  </div>
  <svg class="slide__art" viewBox="0 0 515 308">
    <circle cx="384" cy="154" r="92" fill="var(--grey)"/>
    <circle cx="384" cy="172" r="74" fill="var(--red-dark)"/>
    <circle cx="392" cy="181" r="66" fill="var(--red-deep)"/>
    <text class="chart-label" x="384" y="113" text-anchor="middle" font-size="16" fill="var(--white)">100%</text>
    <text class="chart-label" x="384" y="148" text-anchor="middle" font-size="16" fill="var(--white)">85%</text>
    <text class="chart-label" x="384" y="182" text-anchor="middle" font-size="16" fill="var(--white)">60%</text>
    <rect x="181" y="265" width="82" height="5" fill="var(--grey)"/>
    <rect x="262" y="263" width="92" height="8" fill="var(--red-dark)"/>
    <rect x="353" y="260" width="119" height="11" fill="var(--red-deep)"/>
  </svg>
  <div class="wordmark wordmark--footer">lum-vex, inc.</div>
</section>

<!-- Industries Served -->
<section class="slide slide--industries">
  <div class="slide__header"><h2 class="slide__title">Industries Served</h2><span class="slide__badge"></span></div>
  <div class="copy copy--industries">
    <p>Donec a ultricies purus. Suspendisse dictum nunc nec magna suscipit bibendum. Maecenas turpis sapien, elementum vitae tellus sit amet, efficitur bibendum tortor.</p>
    <p>Sed commodo diam ut nisl sodales consectetur. In hac habitasse platea dictumst. Proin ut augue at augue euismod malesuada.</p>
    <p>Donec a metus sed ligula ultrices vulputate. Nullam convallis interdum mi, in ornare ligula vestibulum vel. Donec faucibus, elit eu viverra posuere, libero enim.</p>
  </div>
  <svg class="slide__art" viewBox="0 0 515 308">
    <g fill="none" stroke="var(--grey)" stroke-width="1.4">
      <polyline points="336,116 360,96 400,96"/>
      <polyline points="366,200 390,178 420,178"/>
      <polyline points="254,252 236,270 190,270"/>
    </g>
    <!-- gear 02 -->
    <circle cx="309" cy="150" r="36" fill="none" stroke="var(--red-deep)" stroke-width="12" stroke-dasharray="8 6.1"/>
    <circle cx="309" cy="150" r="30" fill="none" stroke="var(--red-deep)" stroke-width="10"/>
    <text class="chart-label" x="309" y="158" text-anchor="middle" font-size="24" fill="var(--grey)">02</text>
    <!-- gear 03 -->
    <circle cx="338" cy="234" r="40" fill="none" stroke="var(--grey-light)" stroke-width="12" stroke-dasharray="8.5 7.2"/>
    <circle cx="338" cy="234" r="34" fill="none" stroke="var(--grey-light)" stroke-width="10"/>
    <text class="chart-label" x="338" y="243" text-anchor="middle" font-size="26" fill="var(--grey)">03</text>
    <!-- gear 01 -->
    <circle cx="259" cy="210" r="26" fill="none" stroke="var(--red-dark)" stroke-width="9" stroke-dasharray="6 5"/>
    <circle cx="259" cy="210" r="21" fill="none" stroke="var(--red-dark)" stroke-width="7"/>
    <text class="chart-label" x="259" y="217" text-anchor="middle" font-size="18" fill="var(--grey)">01</text>
    <!-- icons -->
    <circle cx="419" cy="99" r="9" fill="none" stroke="var(--grey)" stroke-width="2.4"/>
    <circle cx="419" cy="99" r="3.5" fill="none" stroke="var(--grey)" stroke-width="2"/>
    <circle cx="442" cy="178" r="8" fill="none" stroke="var(--grey)" stroke-width="2.2"/>
    <polyline points="442,173 442,178 446,180" fill="none" stroke="var(--grey)" stroke-width="1.6"/>
    <circle cx="174" cy="259" r="10" fill="var(--grey)"/>
    <text class="chart-label" x="174" y="263" text-anchor="middle" font-size="11" font-weight="700" fill="var(--white)">$</text>
    <g class="chart-label" font-size="6" fill="var(--text-muted)" text-anchor="middle">
      <text x="420" y="122">2 OPTION</text>
      <text x="420" y="134">Lorem ipsum dolor sit amet,</text>
      <text x="420" y="142">consectetur adipiscing elit, sed do</text>
      <text x="420" y="150">eiusmod tempor.</text>
      <text x="443" y="203">3 OPTION</text>
      <text x="443" y="215">Lorem ipsum dolor sit</text>
      <text x="443" y="223">amet, consectetur</text>
      <text x="443" y="231">adipiscing elit.</text>
      <text x="175" y="210">1 OPTION</text>
      <text x="175" y="222">Lorem ipsum dolor sit</text>
      <text x="175" y="230">amet, consectetur</text>
      <text x="175" y="238">adipiscing elit.</text>
    </g>
  </svg>
  <div class="wordmark wordmark--footer">lum-vex, inc.</div>
</section>

<!-- Principal Represented -->
<section class="slide slide--principals">
  <div class="slide__header"><h2 class="slide__title">Principal Represented</h2><span class="slide__badge"></span></div>
  <svg class="slide__art" viewBox="0 0 515 308">
    <g fill="none" stroke-width="5">
      <circle cx="107" cy="130" r="58" stroke="var(--grey)" pathLength="100"/>
      <circle cx="107" cy="130" r="58" stroke="var(--red-deep)" pathLength="100" stroke-dasharray="62 38" transform="rotate(-60 107 130)"/>
      <circle cx="107" cy="130" r="45" stroke="var(--red-dark)" stroke-width="8" pathLength="100" stroke-dasharray="70 30" transform="rotate(10 107 130)"/>
      <circle cx="107" cy="130" r="32" stroke="var(--grey)" stroke-width="6" pathLength="100" stroke-dasharray="30 70" transform="rotate(-80 107 130)"/>
      <circle cx="107" cy="130" r="32" stroke="var(--red-deep)" stroke-width="6" pathLength="100" stroke-dasharray="55 45" transform="rotate(30 107 130)"/>
      <circle cx="107" cy="130" r="20" stroke="var(--red-deep)" stroke-width="5" pathLength="100" stroke-dasharray="80 20" transform="rotate(20 107 130)"/>

      <circle cx="258" cy="130" r="58" stroke="var(--grey)" stroke-width="3" pathLength="100" stroke-dasharray="75 25" transform="rotate(20 258 130)"/>
      <circle cx="258" cy="130" r="58" stroke="var(--red-deep)" stroke-width="4" pathLength="100" stroke-dasharray="30 70" transform="rotate(-170 258 130)"/>
      <circle cx="258" cy="130" r="47" stroke="var(--red-dark)" stroke-width="7" pathLength="100" stroke-dasharray="55 45" transform="rotate(-150 258 130)"/>
      <circle cx="258" cy="130" r="47" stroke="var(--grey)" stroke-width="7" pathLength="100" stroke-dasharray="18 82" transform="rotate(-10 258 130)"/>
      <circle cx="258" cy="130" r="34" stroke="var(--red-deep)" stroke-width="9" pathLength="100" stroke-dasharray="60 40" transform="rotate(40 258 130)"/>
      <circle cx="258" cy="130" r="22" stroke="var(--red-deep)" stroke-width="5" pathLength="100" stroke-dasharray="78 22" transform="rotate(-20 258 130)"/>

      <circle cx="406" cy="130" r="59" stroke="var(--grey)" stroke-width="3" pathLength="100" stroke-dasharray="20 80" transform="rotate(-95 406 130)"/>
      <circle cx="406" cy="130" r="59" stroke="var(--red-deep)" stroke-width="4" pathLength="100" stroke-dasharray="70 30" transform="rotate(-20 406 130)"/>
      <circle cx="406" cy="130" r="48" stroke="var(--red-dark)" stroke-width="7" pathLength="100" stroke-dasharray="45 55" transform="rotate(90 406 130)"/>
      <circle cx="406" cy="130" r="48" stroke="var(--red-deep)" stroke-width="7" pathLength="100" stroke-dasharray="30 70" transform="rotate(-50 406 130)"/>
      <circle cx="406" cy="130" r="35" stroke="var(--grey)" stroke-width="8" pathLength="100" stroke-dasharray="30 70" transform="rotate(0 406 130)"/>
      <circle cx="406" cy="130" r="35" stroke="var(--red-dark)" stroke-width="8" pathLength="100" stroke-dasharray="45 55" transform="rotate(120 406 130)"/>
      <circle cx="406" cy="130" r="23" stroke="var(--red-deep)" stroke-width="5" pathLength="100" stroke-dasharray="85 15" transform="rotate(-100 406 130)"/>
    </g>
  </svg>
  <ul class="bullets">
    <li>LOREM IPSUM DOLOR sit amet, consectetur adipiscing elit, sed do eiusmod tempor incididunt ut labore et dolore magna aliqua. Ut enim ad minim.</li>
    <li class="is-grey">LOREM IPSUM DOLOR sit amet, consectetur adipiscing elit, sed do eiusmod tempor incididunt ut labore et dolore magna aliqua.</li>
    <li>LOREM IPSUM DOLOR sit amet, consectetur adipiscing elit, sed do eiusmod tempor incididunt ut labore et dolore magna aliqua. Ut enim ad minim veniam.</li>
  </ul>
  <div class="wordmark wordmark--footer">lum-vex, inc.</div>
</section>

<!-- Employee overview -->
<section class="slide slide--employees">
  <div class="slide__header"><h2 class="slide__title">Employee overview</h2><span class="slide__badge"></span></div>
  <svg class="slide__art" viewBox="0 0 515 308">
    <g fill="none" stroke-width="7">
      <circle cx="113" cy="127" r="38" stroke="var(--grey-light)"/>
      <circle cx="113" cy="127" r="38" stroke="var(--red-dark)" pathLength="100" stroke-dasharray="50 50" transform="rotate(-250 113 127)"/>
      <circle cx="113" cy="127" r="38" stroke="var(--amber)" pathLength="100" stroke-dasharray="40 60" transform="rotate(-70 113 127)"/>

      <circle cx="209" cy="127" r="38" stroke="var(--grey-light)"/>
      <circle cx="209" cy="127" r="38" stroke="var(--red-dark)" pathLength="100" stroke-dasharray="38 62" transform="rotate(60 209 127)"/>
      <circle cx="209" cy="127" r="38" stroke="var(--amber)" pathLength="100" stroke-dasharray="30 70" transform="rotate(-190 209 127)"/>

      <circle cx="306" cy="127" r="38" stroke="var(--grey-light)"/>
      <circle cx="306" cy="127" r="38" stroke="var(--red-deep)" pathLength="100" stroke-dasharray="28 72" transform="rotate(30 306 127)"/>
      <circle cx="306" cy="127" r="38" stroke="var(--amber)" pathLength="100" stroke-dasharray="26 74" transform="rotate(130 306 127)"/>

      <circle cx="402" cy="127" r="38" stroke="var(--grey-light)"/>
      <circle cx="402" cy="127" r="38" stroke="var(--red-dark)" pathLength="100" stroke-dasharray="62 38" transform="rotate(-120 402 127)"/>
    </g>
    <g class="chart-label" font-size="15" fill="var(--text-muted)" text-anchor="middle">
      <text x="113" y="132">50%</text><text x="209" y="132">70%</text>
      <text x="306" y="132">55%</text><text x="402" y="132">40%</text>
    </g>
    <g class="chart-label" font-size="7" fill="var(--text-muted)" text-anchor="middle">
      <text x="113" y="193">LOREM IPSUM</text><text x="209" y="193">LOREM IPSUM</text>
      <text x="306" y="193">LOREM IPSUM</text><text x="402" y="193">LOREM IPSUM</text>
    </g>
  </svg>
  <div class="copy copy--employees">
    <p>Donec a ultricies purus. Suspendisse dictum nunc nec magna suscipit bibendum. Maecenas turpis sapien, elementum vitae tellus sit amet, efficitur bibendum tortor.</p>
    <p>Donec a metus sed ligula ultrices vulputate. Nullam convallis interdum mi, in ornare ligula vestibulum vel. Donec faucibus, elit eu viverra posuere, libero enim.</p>
  </div>
  <div class="wordmark wordmark--footer">lum-vex, inc.</div>
</section>

</body>
</html>
```